New Business Card Design Project LORVANTI-Italy

we are LORVANTI-Italy
our company in the market for 3 years we are luxury cosmetic company and its about time for a facelift :)
i will like to have elegant luxurious and unique business card
that will give the person that get it a unique, luxurious and elegant impression
I'm VERY OPEN FOR NEW IDEAS , even duo i add a few files of things that i see on line and i like them

i add my logo as well
my website is LORVANTI.COM
(if you would like to see the main style that we have)

Target Market(s)

adult that have money :)

Industry/Entity Type

Business

Contact Information for Business Card

Name - Dario Lorvanti
Position - CEO and CO Founder
address - 4817 E Halvern
telephone - 555-384-1926
email - dario@lorvanti.com
fax - 555-384-1926
website - LORVANTI.COM

Colors
000000
959595
fbee3e
ffffff

Requirements
Must have
• big logo in GOLD color
• elegant look
• impressive
Nice to have
• not must but maybe classy pattern background
• not must but maybe emblem
• maybe clear plastic business card
Should not have
• colors
• images

```html
<!DOCTYPE html>
<html lang="en">
<head>
<meta charset="utf-8">
<title>LORVANTI-Italy Business Card</title>
<link rel="stylesheet" href="https://fonts.googleapis.com/css2?family=Crimson+Text:wght@400;600&display=swap">
<style>
  :root {
    --page: #d9d4cd;
    --frost-light: #f1efec;
    --gold: #c9a24a;
    --gold-deep: #a77f2c;
    --ink-light: #f2f2f2;
  }
  * { margin: 0; padding: 0; box-sizing: border-box; }
  html, body {
    width: 1200px; height: 970px; overflow: hidden;
    background: var(--page);
  }
  .canvas { position: relative; width: 1200px; height: 970px; }
  .card {
    position: absolute; left: 100px; top: 201px;
    width: 1000px; height: 568px;
    border-radius: 22px; overflow: hidden;
    box-shadow: 0 18px 40px rgba(0,0,0,0.25);
    font-family: "Crimson Text", Georgia, serif;
  }
  .card-art { position: absolute; inset: 0; }
  .contact {
    position: absolute; left: 71px; top: 100px;
    color: var(--ink-light);
  }
  .contact .name { font-size: 36px; font-weight: 600; color: var(--gold); line-height: 1.1; }
  .contact .role { font-size: 26px; line-height: 1.3; }
  .contact .company { margin-top: 36px; font-size: 27px; font-weight: 600; color: var(--gold); line-height: 1.2; }
  .contact .address { font-size: 26px; line-height: 1.35; }
  .lines { margin-top: 32px; list-style: none; }
  .lines li { display: flex; align-items: center; gap: 12px; font-size: 26px; line-height: 37px; }
  .lines svg { width: 22px; height: 22px; fill: var(--gold); flex: none; }
  .brand {
    position: absolute; left: 548px; top: 125px; width: 400px;
    display: flex; flex-direction: column; align-items: center;
    color: var(--gold-deep);
  }
  .brand .mark {
    width: 160px; height: 160px; margin-bottom: 30px;
    border: 5px solid var(--gold-deep); border-radius: 50%;
  }
  .brand .name-set { font-size: 44px; font-weight: 600; line-height: 1.1; }
  .brand .rule { width: 360px; height: 3px; margin-top: 40px; background: var(--gold-deep); }
  .brand .place { margin-top: 8px; font-size: 24px; font-weight: 600; line-height: 1.2; }
</style>
</head>
<body>
<main class="canvas">
  <section class="card">
    <svg class="card-art" width="1000" height="568" viewBox="0 0 1000 568" aria-hidden="true">
      <defs>
        <linearGradient id="frost" x1="0" y1="0" x2="1" y2="1">
          <stop offset="0" stop-color="#ece8e3"/>
          <stop offset="0.5" stop-color="#f6f5f3"/>
          <stop offset="1" stop-color="#cfcbc6"/>
        </linearGradient>
        <radialGradient id="panel" cx="0.25" cy="0.55" r="0.75">
          <stop offset="0" stop-color="#3d3d3d"/>
          <stop offset="0.6" stop-color="#1a1a1a"/>
          <stop offset="1" stop-color="#060606"/>
        </radialGradient>
        <linearGradient id="goldline" x1="0" y1="0" x2="0" y2="1">
          <stop offset="0" stop-color="#e2c06a"/>
          <stop offset="0.5" stop-color="#a87b28"/>
          <stop offset="1" stop-color="#d7b25a"/>
        </linearGradient>
      </defs>
      <rect width="1000" height="568" fill="url(#frost)"/>
      <path d="M0 0 H700 C540 40 455 160 455 290 C455 420 540 520 680 568 H0 Z" fill="url(#panel)"/>
      <path d="M700 0 C540 40 455 160 455 290 C455 420 540 520 680 568" fill="none" stroke="url(#goldline)" stroke-width="4"/>
    </svg>

    <div class="contact">
      <p class="name">Dario Lorvanti</p>
      <p class="role">CEO and CO Founder</p>
      <p class="company">LORVANTI-Italy</p>
      <p class="address">4817 E Halvern</p>
      <ul class="lines">
        <li><svg viewBox="0 0 24 24"><path d="M6.6 10.8a15.2 15.2 0 0 0 6.6 6.6l2.2-2.2c.3-.3.7-.4 1-.2 1.1.4 2.3.6 3.6.6.6 0 1 .4 1 1V20c0 .6-.4 1-1 1C10.6 21 3 13.4 3 4c0-.6.4-1 1-1h3.5c.6 0 1 .4 1 1 0 1.3.2 2.5.6 3.6.1.3 0 .7-.2 1z"/></svg>555-384-1926</li>
        <li><svg viewBox="0 0 24 24"><path d="M6 2h10l2 2v5H6zM3 10h18a1 1 0 0 1 1 1v7h-4v4H6v-4H2v-7a1 1 0 0 1 1-1zm5 6v4h8v-4z"/></svg>555-384-1926</li>
        <li><svg viewBox="0 0 24 24"><path d="M2 5h20v14H2zm2 2v.4l8 5.2 8-5.2V7zm0 2.8V17h16V9.8l-8 5.2z"/></svg>dario@lorvanti.com</li>
        <li><svg viewBox="0 0 24 24"><path d="M12 2a10 10 0 1 0 0 20 10 10 0 0 0 0-20zm6.9 6h-3a15 15 0 0 0-1.3-3.9A8 8 0 0 1 18.9 8zM12 4c.9 1.2 1.6 2.6 2 4h-4c.4-1.4 1.1-2.8 2-4zM4.3 14a8 8 0 0 1 0-4h3.4a16 16 0 0 0 0 4zm.8 2h3a15 15 0 0 0 1.3 3.9A8 8 0 0 1 5.1 16zm3-8h-3a8 8 0 0 1 4.3-3.9A15 15 0 0 0 8.1 8zM12 20c-.9-1.2-1.6-2.6-2-4h4c-.4 1.4-1.1 2.8-2 4zm2.3-6H9.7a14 14 0 0 1 0-4h4.6a14 14 0 0 1 0 4zm.3 5.9A15 15 0 0 0 15.9 16h3a8 8 0 0 1-4.3 3.9zm1.7-5.9a16 16 0 0 0 0-4h3.4a8 8 0 0 1 0 4z"/></svg>LORVANTI.COM</li>
      </ul>
    </div>

    <div class="brand">
      <div class="mark"></div>
      <p class="name-set">LORVANTI</p>
      <div class="rule"></div>
      <p class="place">ITALY</p>
    </div>
  </section>
</main>
</body>
</html>
```